Executive & Leadership Coach needs a Graphic Design

We need a graphic design for a Leadership methodology/strategy that can be linked to The Harbor Prism

The Harbor Prism consists of:
1. Achievements
2. Personal Brand
3. Network
4. Executive Presence

This should Graphic Design will need to be used in PowerPoint presentations, training manuals and web pages

The design should be modern and provide the feeling of strength, trust, energy & creativity

Industry/Entity Type

Graphic Design

Font styles to use
Other font styles liked:
• Calibri, Verdana

```html
<!DOCTYPE html>
<html lang="en">
<head>
<meta charset="utf-8">
<title>The Harbor Prism</title>
<link rel="stylesheet" href="https://fonts.googleapis.com/css2?family=Open+Sans:wght@600;700;800&display=swap">
<style>
  :root {
    --canvas-bg: #ffffff;
    --label-white: #ffffff;
    --hub-text: #3b3b3b;
    --blue-deep: #1c70b8;
    --blue-light: #29aee3;
    --green-yellow: #e3e41f;
    --green: #8cc63f;
    --magenta-deep: #d81b60;
    --magenta: #ec008c;
    --purple-light: #9b2a92;
    --purple-deep: #5f2e91;
    --silver-light: #f7f7f7;
    --silver-mid: #c9c9cb;
    --silver-dark: #9a9a9d;
  }
  html, body {
    margin: 0;
    padding: 0;
    width: 1200px;
    height: 1000px;
    overflow: hidden;
    background: var(--canvas-bg);
  }
  .canvas {
    width: 1200px;
    height: 1000px;
    position: relative;
  }
  .prism-wheel {
    display: block;
    width: 1200px;
    height: 1000px;
  }
  .segment-label {
    font-family: "Open Sans", Calibri, Verdana, sans-serif;
    font-weight: 800;
    font-size: 40px;
    fill: var(--label-white);
    letter-spacing: 0.5px;
  }
  .hub-title {
    font-family: "Open Sans", Calibri, Verdana, sans-serif;
    font-weight: 600;
    font-size: 46px;
    fill: var(--hub-text);
  }
</style>
</head>
<body>
<main class="canvas">
  <svg class="prism-wheel" viewBox="0 0 1200 1000" xmlns="http://www.w3.org/2000/svg" aria-labelledby="wheel-title">
    <title id="wheel-title">The Harbor Prism: Executive Presence, Achievements, Personal, Network</title>
    <defs>
      <linearGradient id="grad-presence" x1="0" y1="0" x2="1" y2="1">
        <stop offset="0" stop-color="var(--blue-deep)"/>
        <stop offset="1" stop-color="var(--blue-light)"/>
      </linearGradient>
      <linearGradient id="grad-achievements" x1="0" y1="1" x2="1" y2="0">
        <stop offset="0" stop-color="var(--green-yellow)"/>
        <stop offset="0.55" stop-color="var(--green)"/>
        <stop offset="1" stop-color="var(--green)"/>
      </linearGradient>
      <linearGradient id="grad-personal" x1="0" y1="1" x2="1" y2="0">
        <stop offset="0" stop-color="var(--magenta-deep)"/>
        <stop offset="1" stop-color="var(--magenta)"/>
      </linearGradient>
      <linearGradient id="grad-network" x1="0" y1="0" x2="1" y2="1">
        <stop offset="0" stop-color="var(--purple-light)"/>
        <stop offset="1" stop-color="var(--purple-deep)"/>
      </linearGradient>
      <linearGradient id="grad-silver" x1="0" y1="0" x2="1" y2="0">
        <stop offset="0" stop-color="var(--silver-dark)"/>
        <stop offset="0.2" stop-color="var(--silver-light)"/>
        <stop offset="0.45" stop-color="var(--silver-mid)"/>
        <stop offset="0.7" stop-color="var(--silver-light)"/>
        <stop offset="1" stop-color="var(--silver-dark)"/>
      </linearGradient>
      <radialGradient id="grad-hub" cx="0.5" cy="0.45" r="0.6">
        <stop offset="0.7" stop-color="#ffffff"/>
        <stop offset="1" stop-color="#e6e6e8"/>
      </radialGradient>

      <path id="arc-presence" d="M320,500 A280,280 0 0 1 600,220"/>
      <path id="arc-achievements" d="M600,220 A280,280 0 0 1 880,500"/>
      <path id="arc-personal" d="M302,500 A298,298 0 0 0 600,798"/>
      <path id="arc-network" d="M600,798 A298,298 0 0 0 898,500"/>
    </defs>

    <!-- outer rim -->
    <circle class="outer-rim" cx="600" cy="500" r="366" fill="url(#grad-silver)" stroke="var(--silver-dark)" stroke-width="2"/>
    <circle class="rim-edge" cx="600" cy="500" r="335" fill="none" stroke="var(--silver-dark)" stroke-width="1.5"/>

    <!-- quadrants -->
    <g class="segments" stroke="#ffffff" stroke-width="4">
      <path class="segment segment-presence" d="M600,500 L267,500 A333,333 0 0 1 600,167 Z" fill="url(#grad-presence)"/>
      <path class="segment segment-achievements" d="M600,500 L600,167 A333,333 0 0 1 933,500 Z" fill="url(#grad-achievements)"/>
      <path class="segment segment-personal" d="M600,500 L600,833 A333,333 0 0 1 267,500 Z" fill="url(#grad-personal)"/>
      <path class="segment segment-network" d="M600,500 L933,500 A333,333 0 0 1 600,833 Z" fill="url(#grad-network)"/>
    </g>

    <!-- labels -->
    <text class="segment-label"><textPath href="#arc-presence" startOffset="50%" text-anchor="middle">Executive Presence</textPath></text>
    <text class="segment-label"><textPath href="#arc-achievements" startOffset="50%" text-anchor="middle">Achievements</textPath></text>
    <text class="segment-label"><textPath href="#arc-personal" startOffset="50%" text-anchor="middle">Personal</textPath></text>
    <text class="segment-label"><textPath href="#arc-network" startOffset="50%" text-anchor="middle">Network</textPath></text>

    <!-- hub -->
    <circle class="hub-ring" cx="600" cy="500" r="142" fill="url(#grad-silver)" stroke="var(--silver-dark)" stroke-width="2"/>
    <circle class="hub-face" cx="600" cy="500" r="120" fill="url(#grad-hub)" stroke="var(--silver-mid)" stroke-width="1.5"/>
    <text class="hub-title" x="600" y="488" text-anchor="middle">Harbor</text>
    <text class="hub-title" x="600" y="542" text-anchor="middle">Prism</text>
  </svg>
</main>
</body>
</html>
```